Design a large parking banner – mandatory ticket validation in the shop

Banner Size:
548 cm (width) x 154 cm (height)
Note: The banner will be placed in a metal frame at our parking lot entrance, fully visible to every incoming truck driver. The message must be easy to read from a distance.
Goal of the Banner:
To inform all truck drivers that they must validate their entry ticket inside the shop, even if they are parking for a short time.
The message must be displayed in multiple languages for international drivers.
Mandatory Content:
Main message – in multiple languages (clearly separated or stacked):
Dutch (NL): Vergeet je ticket niet te valideren in de shop – verplicht, ook bij kort parkeren!
French (FR): N'oubliez pas de valider votre ticket à la boutique – obligatoire, même pour un court arrêt !
English (EN): Don't forget to validate your entry ticket in the shop – mandatory, even for short stops!
German (DE): Vergessen Sie nicht, Ihr Einfahrticket im Shop zu entwerten – Pflicht, auch bei kurzem Parken!
Polish (PL): Nie zapomnij zatwierdzić biletu w sklepie – obowiązkowe, nawet przy krótkim postoju!
Romanian (RO): Nu uitați să validați biletul în magazin – obligatoriu, chiar și pentru opriri scurte!
You can include more languages if space allows, but these are essential.
Opening Hours Block (in one section below):
Shop Opening Hours
Mon – Fri: 05:30 – 22:00
Sat & Sun: 08:00 – 22:00
Style & Branding:
The design must match the visual identity of Haulport 41Ter
Please refer to the attached photos of existing parking signage for guidance on colors, typography, and layout style
Our logo (attached) must be clearly visible and professionally integrated
Feel free to use icons or pictograms to visually support the message (e.g., ticket, truck, arrow)
Readability is key – large, bold text and high contrast colors that are visible from a distance
Target Audience:
International truck drivers – people who need fast, clear communication. Not everyone speaks the local language, so visual clarity and multilingual messaging are critical.
File Requirements:
Print-ready file (PDF or EPS) – 300 dpi at 1:10 scale
Include 5 cm bleed on all sides
Provide open source files if possible (AI or PSD)

```html
<!DOCTYPE html>
<html lang="en">
<head>
<meta charset="utf-8">
<title>Haulport 41Ter – Ticket Validation Banner</title>
<link href="https://fonts.googleapis.com/css2?family=Roboto+Condensed:wght@400;700&display=swap" rel="stylesheet">
<style>
  :root {
    --navy: #1b2148;
    --red: #d3181f;
    --blue: #1b7fcb;
    --white: #ffffff;
    --backdrop: #e6e9ee;
  }
  * { box-sizing: border-box; margin: 0; padding: 0; }
  html, body {
    width: 1200px; height: 840px; overflow: hidden;
    background: var(--backdrop);
    font-family: "Roboto Condensed", "Arial Narrow", sans-serif;
  }
  .banner {
    position: absolute; left: 30px; top: 260px;
    width: 1140px; height: 320px;
    background: var(--navy); color: var(--white);
    overflow: hidden;
  }
  .banner-header {
    position: absolute; left: 22px; top: 12px; right: 22px; height: 46px;
    display: flex; align-items: center; gap: 22px;
    border-bottom: 3px solid var(--red);
  }
  .brand-name {
    font-weight: 700; font-size: 24px; color: var(--white);
    letter-spacing: 0.5px; white-space: nowrap;
  }
  .headline {
    font-weight: 700; font-size: 31px; white-space: nowrap; line-height: 1;
  }
  .notice {
    position: absolute; left: 24px; top: 68px; width: 860px;
  }
  .notice-title {
    display: flex; align-items: center; gap: 6px;
    font-size: 21px; line-height: 26px; margin-bottom: 2px;
  }
  .alert-icon {
    width: 22px; height: 22px; border: 2px solid var(--red); border-radius: 50%;
    display: flex; align-items: center; justify-content: center;
    font-weight: 700; font-size: 15px;
  }
  .language-list { list-style: none; }
  .language-list li {
    font-size: 17px; line-height: 34px; white-space: nowrap;
    padding-left: 24px; position: relative;
  }
  .language-list li::before {
    content: "››"; color: var(--red); position: absolute; left: 2px;
    font-size: 19px; font-weight: 700;
  }
  .sidebar {
    position: absolute; right: 28px; top: 68px; width: 220px;
    display: flex; flex-direction: column; align-items: center;
  }
  .parking-sign {
    width: 58px; height: 76px; background: var(--blue);
    border: 3px solid var(--white); border-radius: 9px;
    font-weight: 700; font-size: 60px; line-height: 70px; text-align: center;
  }
  .parking-post { width: 6px; height: 6px; background: var(--white); }
  .parking-arrow {
    background: var(--white); color: var(--navy);
    font-size: 22px; padding: 3px 10px; white-space: nowrap; line-height: 1.2;
  }
  .hours-title {
    margin-top: 10px; background: var(--blue);
    font-weight: 700; font-size: 21px; line-height: 1.2;
    padding: 3px 8px; border-radius: 4px; white-space: nowrap;
  }
  .hours-row {
    margin-top: 7px; font-size: 19px; line-height: 1.2; padding-bottom: 2px;
    border-bottom: 3px solid var(--red); white-space: nowrap;
  }
</style>
</head>
<body>
  <main class="banner">
    <header class="banner-header">
      <span class="brand-name">HAULPORT 41TER</span>
      <h1 class="headline">"Attention Drivers: Entry Tickets Must Be Verified Inside the Shop."</h1>
    </header>

    <section class="notice">
      <h2 class="notice-title"><span class="alert-icon">!</span>MUST READ!</h2>
      <ul class="language-list">
        <li>English (EN): Don't forget to validate your entry ticket in the shop – mandatory, even for short stops!</li>
        <li>French (FR): N'oubliez pas de valider votre ticket à la boutique – obligatoire, même pour un court arrêt !</li>
        <li>Dutch (NL): Vergeet je ticket niet te valideren in de shop – verplicht, ook bij kort parkeren!</li>
        <li>German (DE): Vergessen Sie nicht, Ihr Einfahrticket im Shop zu entwerten – Pflicht, auch bei kurzem Parken!</li>
        <li>Polish (PL): Nie zapomnij zatwierdzić biletu w sklepie – obowiązkowe, nawet przy krótkim postoju!</li>
        <li>Romanian (RO): Nu uitați să validați biletul în magazin – obligatoriu, chiar și pentru opriri scurte!</li>
      </ul>
    </section>

    <aside class="sidebar">
      <div class="parking-sign">P</div>
      <div class="parking-post"></div>
      <div class="parking-arrow">←PARKING→</div>
      <div class="hours-title">SHOP OPENING HOURS</div>
      <div class="hours-row">MON – FRI: 05:30 – 22:00</div>
      <div class="hours-row">SAT &amp; SUN: 08:00 – 22:00</div>
    </aside>
  </main>
</body>
</html>
```